Simple and Clean business card design

We would like the design to be simple clean and to incorporate our colors.

We are open to your design and talent, we have the dots in our logo as we think of it as data points and we connect data points for people.

We are open to see the great creative and clean design you bring to the table

Contact Information for Business Card

please include: name, position, email, phone and website

Font styles to use
Sans Serif

Requirements
Must have
• my colors incorporated, simplicity
Nice to have
• lots of white space, simplicity
Should not have
• complexicity/ complex art

```html
<!DOCTYPE html>
<html lang="en">
<head>
<meta charset="utf-8">
<title>Nodeway Business Card</title>
<link rel="stylesheet" href="https://fonts.googleapis.com/css2?family=Lato:wght@700&family=Arimo:wght@400&display=swap">
<style>
  :root {
    --backdrop: #555555;
    --card-blue: #4585f4;
    --card-black: #1e1d1c;
    --ink-white: #ffffff;
    --dot-blue: #4585f4;
  }
  * { margin: 0; padding: 0; box-sizing: border-box; }
  html, body {
    width: 1093px;
    height: 1200px;
    overflow: hidden;
    background: var(--backdrop);
  }
  .canvas {
    position: relative;
    width: 1093px;
    height: 1200px;
  }
  .card {
    position: absolute;
    left: 264px;
    width: 580px;
    height: 357px;
  }
  .card--front {
    top: 226px;
    background: var(--card-blue);
    color: var(--ink-white);
    text-align: center;
  }
  .card--back {
    top: 620px;
    background: var(--card-black);
    display: flex;
    align-items: center;
    justify-content: center;
  }
  .holder-name {
    position: absolute;
    top: 84px;
    width: 100%;
    font-family: "Lato", sans-serif;
    font-weight: 700;
    font-size: 30px;
    letter-spacing: -0.3px;
    line-height: 1;
  }
  .holder-title {
    position: absolute;
    top: 118px;
    width: 100%;
    font-family: "Arimo", sans-serif;
    font-size: 19px;
    line-height: 1;
  }
  .contact-icons {
    position: absolute;
    top: 157px;
    left: 50%;
    transform: translateX(-50%);
  }
  .contact-list {
    position: absolute;
    top: 193px;
    width: 100%;
    list-style: none;
    font-family: "Arimo", sans-serif;
    font-size: 19px;
    line-height: 27.5px;
  }
  .brand {
    display: flex;
    align-items: center;
    gap: 14px;
    margin-top: 12px;
  }
  .brand-dot {
    width: 22px;
    height: 22px;
    border-radius: 50%;
    background: var(--dot-blue);
  }
  .brand-name {
    font-family: "Lato", sans-serif;
    font-weight: 700;
    font-size: 70px;
    color: var(--ink-white);
    line-height: 1;
  }
</style>
</head>
<body>
<main class="canvas">
  <section class="card card--front" aria-label="Card front">
    <h1 class="holder-name">DANA WHITFIELD</h1>
    <p class="holder-title">Founder/ CEO</p>
    <svg class="contact-icons" width="148" height="28" viewBox="0 0 148 28" fill="none" stroke="#ffffff" stroke-width="2" aria-hidden="true">
      <line x1="0" y1="14" x2="23" y2="14" stroke-width="1"/>
      <line x1="125" y1="14" x2="148" y2="14" stroke-width="1"/>
      <circle cx="42" cy="14" r="12"/>
      <path d="M37 9.5c0 5 3.5 9 8.5 9.5l2-2-2.5-2-1.5 1c-1.5-.8-2.7-2-3.5-3.5l1-1.5-2-2.5z" stroke-width="1.4" stroke-linejoin="round"/>
      <circle cx="74" cy="14" r="12"/>
      <rect x="67" y="9.5" width="14" height="9" stroke-width="1.4"/>
      <path d="M67 9.5l7 5.5 7-5.5" stroke-width="1.4"/>
      <circle cx="104" cy="14" r="12"/>
      <circle cx="104" cy="14" r="7" stroke-width="1.3"/>
      <ellipse cx="104" cy="14" rx="3" ry="7" stroke-width="1.1"/>
      <line x1="97" y1="14" x2="111" y2="14" stroke-width="1.1"/>
      <line x1="98" y1="10.5" x2="110" y2="10.5" stroke-width="1"/>
      <line x1="98" y1="17.5" x2="110" y2="17.5" stroke-width="1"/>
    </svg>
    <ul class="contact-list">
      <li class="contact-phone">555-214-0387</li>
      <li class="contact-email">dana.whitfield@nodeway.one</li>
      <li class="contact-web">www.Nodeway.one</li>
    </ul>
  </section>
  <section class="card card--back" aria-label="Card back">
    <div class="brand">
      <span class="brand-dot"></span>
      <span class="brand-name">Nodeway</span>
    </div>
  </section>
</main>
</body>
</html>
```